Solvane Restaurant
Truly Tropical
Simple
#41 Estate Coral
(at the Harbor Palm Cottages)
Tidewater Key, TK 00910
Solvane_Restaurant@mailbreeze.example
www.solvaneisle.example
* Free Wi-fi
* Special events venue-mediations, meetings, fund raisers, wedding receptions, catering, private parties, you name it we can host it !!
* Superior customer service
* Delicious cuisine
please use this logo

```html
<!DOCTYPE html>
<html lang="en">
<head>
<meta charset="utf-8">
<title>Solvane Restaurant — Stationery Set</title>
<link rel="stylesheet" href="https://fonts.googleapis.com/css2?family=Cormorant+Garamond:wght@500&family=Lato:wght@400;700&display=swap">
<style>
  :root {
    --canvas: #efefef;
    --paper: #ffffff;
    --edge: #d9d9d9;
    --teal: #7cc4bc;
    --teal-soft: #cfe9e5;
    --teal-faint: #eef7f5;
    --gold: #d9a441;
    --ink: #555a5a;
    --cell: #dedede;
    --line: #8a8a8a;
  }
  * { box-sizing: border-box; margin: 0; padding: 0; }
  html, body { width: 1200px; height: 552px; overflow: hidden; background: var(--canvas); }
  body { position: relative; font-family: "Lato", sans-serif; color: var(--ink); }

  .sheet { position: absolute; background: var(--paper); border: 1px solid var(--edge); box-shadow: 0 1px 3px rgba(0,0,0,.12); }
  .letterhead { top: 12px; height: 511px; }
  .letterhead--fax { left: 22px; width: 362px; }
  .letterhead--plain { left: 403px; width: 346px; }
  .card { top: 20px; height: 88px; }
  .card--back { left: 780px; width: 209px; }
  .card--front { left: 1008px; width: 163px; }
  .envelope { left: 780px; width: 396px; height: 187px; }
  .envelope--front { top: 125px; }
  .envelope--back { top: 336px; }

  .brand { position: absolute; display: flex; align-items: center; gap: 4px; white-space: nowrap; }
  .brand__dot { width: 9px; height: 9px; border-radius: 50%; background: var(--teal-soft); }
  .brand__name { font-family: "Cormorant Garamond", serif; font-weight: 500; color: var(--teal); font-size: 22px; line-height: 1; }
  .brand--sm .brand__name { font-size: 14px; }
  .brand--sm .brand__dot { width: 6px; height: 6px; }

  .side-flourish { position: absolute; width: 12px; height: 110px; border-radius: 6px;
    background: linear-gradient(180deg, var(--teal-faint), var(--teal-soft) 45%, var(--teal) 55%, var(--teal-faint)); }
  .floral-wash { position: absolute; border-radius: 50%;
    background: radial-gradient(ellipse at center, var(--teal-faint), rgba(255,255,255,0) 70%); }

  .footer { position: absolute; left: 20px; right: 20px; text-align: center; font-size: 5.5px; line-height: 1.5; color: var(--gold); letter-spacing: .2px; }

  .fax-label { position: absolute; right: 22px; top: 78px; font-size: 11px; font-weight: 700; color: #333; }
  .fax-table { position: absolute; left: 14px; top: 94px; width: 336px; border-collapse: collapse; font-size: 6px; }
  .fax-table td { border: 1px solid var(--line); height: 19px; padding: 0 4px; }
  .fax-table .cell-label { background: var(--cell); width: 44px; }
  .checks { position: absolute; left: 14px; top: 180px; display: flex; gap: 20px; font-size: 6px; }
  .checks span { display: flex; align-items: center; gap: 3px; }
  .checks i { width: 6px; height: 6px; border: 1px solid var(--line); display: inline-block; }

  .card-text { position: absolute; font-size: 5.5px; line-height: 1.45; color: var(--gold); white-space: nowrap; }
</style>
</head>
<body>

<section class="sheet letterhead letterhead--fax">
  <div class="brand" style="left:16px; top:16px;"><span class="brand__dot"></span><span class="brand__name">Solvane</span></div>
  <div class="fax-label">FAX</div>
  <table class="fax-table">
    <tr><td class="cell-label">To:</td><td></td><td class="cell-label">From:</td><td></td></tr>
    <tr><td class="cell-label">Fax:</td><td></td><td class="cell-label">Pages:</td><td></td></tr>
    <tr><td class="cell-label">Phone:</td><td></td><td class="cell-label">Date:</td><td></td></tr>
    <tr><td class="cell-label">Re:</td><td></td><td class="cell-label">CC:</td><td></td></tr>
  </table>
  <div class="checks">
    <span><i></i>Urgent</span><span><i></i>For Review</span><span><i></i>Please Comment</span><span><i></i>Please Reply</span><span><i></i>Please Recycle</span>
  </div>
  <div class="side-flourish" role="img" aria-label="Teal curled ribbon flourish" style="left:-6px; top:215px;"></div>
  <div class="side-flourish" role="img" aria-label="Teal curled ribbon flourish" style="right:-6px; top:215px;"></div>
  <div class="floral-wash" role="img" aria-label="Faint floral branch illustration" style="left:70px; top:340px; width:210px; height:130px;"></div>
  <p class="footer" style="top:486px;">#41 Estate Coral (at the Harbor Palm Cottages) Tidewater Key, TK 00910 · Solvane_Restaurant@mailbreeze.example<br>www.solvaneisle.example</p>
</section>

<section class="sheet letterhead letterhead--plain">
  <div class="brand" style="left:16px; top:16px;"><span class="brand__dot"></span><span class="brand__name">Solvane</span></div>
  <div class="side-flourish" role="img" aria-label="Teal curled ribbon flourish" style="left:-6px; top:215px;"></div>
  <div class="floral-wash" role="img" aria-label="Faint floral branch illustration" style="left:65px; top:340px; width:210px; height:130px;"></div>
  <p class="footer" style="top:486px;">#41 Estate Coral (at the Harbor Palm Cottages) Tidewater Key, TK 00910 · Solvane_Restaurant@mailbreeze.example<br>www.solvaneisle.example</p>
</section>

<section class="sheet card card--back">
  <div class="brand brand--sm" style="left:8px; top:8px;"><span class="brand__dot"></span><span class="brand__name">Solvane</span></div>
  <p class="card-text" style="left:80px; top:10px;">Reservations Desk<br>Truly Tropical Dining</p>
  <p class="card-text" style="left:8px; top:48px;">#41 Estate Coral, Tidewater Key, TK 00910<br>Solvane_Restaurant@mailbreeze.example<br>www.solvaneisle.example</p>
</section>

<section class="sheet card card--front">
  <div class="brand brand--sm" style="left:8px; top:10px;"><span class="brand__dot"></span><span class="brand__name">Solvane</span></div>
  <p class="card-text" style="left:8px; top:34px;">Truly Tropical</p>
</section>

<section class="sheet envelope envelope--front">
  <div class="brand" style="left:12px; top:12px;"><span class="brand__dot"></span><span class="brand__name">Solvane</span></div>
  <div class="side-flourish" role="img" aria-label="Teal curled ribbon flourish" style="left:-6px; top:40px; height:90px;"></div>
  <div class="floral-wash" role="img" aria-label="Faint floral branch illustration" style="left:200px; top:40px; width:180px; height:100px;"></div>
  <p class="footer" style="top:166px;">#41 Estate Coral (at the Harbor Palm Cottages) Tidewater Key, TK 00910 · www.solvaneisle.example</p>
</section>

<section class="sheet envelope envelope--back">
  <div class="brand" style="left:50%; top:18px; transform:translateX(-50%);"><span class="brand__dot"></span><span class="brand__name">Solvane</span></div>
  <div class="side-flourish" role="img" aria-label="Teal curled ribbon flourish" style="left:-6px; top:40px; height:90px;"></div>
  <p class="footer" style="top:166px;">#41 Estate Coral (at the Harbor Palm Cottages) Tidewater Key, TK 00910 · www.solvaneisle.example</p>
</section>

</body>
</html>
```